"Harbor Builders" is a residential building company and needs a new business card design and may re

We would like a redesign based on the existing logo, and would like to see a new font as well. We are bespoke home builders who build sustainable energy efficient homes.

Industry/Entity Type

Construction

Contact Information for Business Card

Business card size 40mm x 90mm

Colors

Designer to choose colors to be used in the design.

```html
<!DOCTYPE html>
<html lang="en">
<head>
<meta charset="utf-8">
<title>Harbor Builders – Business Card</title>
<link rel="stylesheet" href="https://fonts.googleapis.com/css2?family=Open+Sans:wght@400;600;700&family=Roboto:wght@400;500;700&family=Roboto+Condensed:wght@700&display=swap">
<style>
  :root {
    --backdrop: #2b2b2b;
    --card-light: #fbfbfb;
    --card-dark: #242424;
    --ink: #1c1c1c;
    --ink-muted: #5a5a5a;
    --lime: #c4e02a;
    --white: #f4f4f4;
    --divider: #8a8a8a;
  }
  * { margin: 0; padding: 0; box-sizing: border-box; }
  html, body {
    width: 1200px;
    height: 900px;
    overflow: hidden;
    background: var(--backdrop);
  }
  .canvas {
    width: 1200px;
    height: 900px;
    display: flex;
    flex-direction: column;
    align-items: center;
    justify-content: center;
    gap: 40px;
  }
  .card {
    width: 720px;
    height: 320px;
    position: relative;
  }
  .card--front {
    background: var(--card-light);
    display: flex;
    flex-direction: column;
    align-items: center;
  }
  .brand {
    margin-top: 112px;
    display: flex;
    align-items: center;
    gap: 18px;
  }
  .brand__square {
    width: 34px;
    height: 34px;
    background: var(--lime);
  }
  .brand__name {
    font-family: "Open Sans", sans-serif;
    font-weight: 700;
    font-size: 48px;
    letter-spacing: -0.5px;
    color: var(--ink);
    line-height: 1;
  }
  .front__url {
    position: absolute;
    bottom: 44px;
    left: 0;
    right: 0;
    text-align: center;
    font-family: "Open Sans", sans-serif;
    font-size: 15px;
    letter-spacing: 4px;
    color: var(--ink-muted);
  }
  .card--back {
    background: var(--card-dark);
    font-family: "Roboto", sans-serif;
    color: var(--white);
  }
  .back__top {
    position: absolute;
    top: 62px;
    left: 0;
    right: 0;
    display: flex;
    justify-content: center;
    align-items: center;
  }
  .holder-name {
    font-family: "Roboto Condensed", sans-serif;
    font-weight: 700;
    font-size: 32px;
    color: var(--lime);
    text-transform: uppercase;
    padding-right: 30px;
  }
  .back__divider {
    width: 1px;
    height: 96px;
    background: var(--divider);
  }
  .contact-list {
    list-style: none;
    padding-left: 26px;
    display: flex;
    flex-direction: column;
    gap: 6px;
  }
  .contact-list__item {
    display: flex;
    align-items: center;
    gap: 12px;
    font-size: 18px;
    font-weight: 500;
  }
  .contact-list__icon {
    width: 18px;
    height: 18px;
    flex: none;
  }
  .company-details {
    position: absolute;
    bottom: 40px;
    left: 0;
    right: 0;
    text-align: center;
    font-size: 18px;
    line-height: 1.3;
  }
  .company-details__name { font-weight: 700; }
</style>
</head>
<body>
<main class="canvas">
  <section class="card card--front">
    <div class="brand">
      <span class="brand__square"></span>
      <span class="brand__name">Harbor Builders</span>
    </div>
    <p class="front__url">www.harborbuilders.com.au</p>
  </section>

  <section class="card card--back">
    <div class="back__top">
      <h1 class="holder-name">Daniel Moretti</h1>
      <span class="back__divider"></span>
      <ul class="contact-list">
        <li class="contact-list__item">
          <svg class="contact-list__icon" viewBox="0 0 18 18" aria-hidden="true">
            <rect x="4.5" y="1" width="9" height="16" rx="1.5" fill="none" stroke="var(--lime)" stroke-width="2"/>
            <rect x="7.5" y="13.5" width="3" height="1.5" fill="var(--lime)"/>
          </svg>
          <span>0400 318 726</span>
        </li>
        <li class="contact-list__item">
          <svg class="contact-list__icon" viewBox="0 0 18 18" aria-hidden="true">
            <rect x="1" y="4" width="16" height="11" fill="var(--lime)"/>
            <polyline points="1,4 9,10.5 17,4" fill="none" stroke="var(--card-dark)" stroke-width="1.5"/>
          </svg>
          <span>daniel@harborbuilders.com.au</span>
        </li>
        <li class="contact-list__item">
          <svg class="contact-list__icon" viewBox="0 0 18 18" aria-hidden="true">
            <circle cx="9" cy="9" r="7.5" fill="var(--lime)"/>
            <ellipse cx="9" cy="9" rx="3.2" ry="7.5" fill="none" stroke="var(--card-dark)" stroke-width="1.3"/>
            <line x1="1.5" y1="9" x2="16.5" y2="9" stroke="var(--card-dark)" stroke-width="1.3"/>
          </svg>
          <span>www.harborbuilders.com.au</span>
        </li>
      </ul>
    </div>
    <address class="company-details" style="font-style: normal;">
      <div class="company-details__name">Harbor Builders Pty Ltd</div>
      <div>PO Box 4120 Northgate, LPO Eastfield WA 6099</div>
      <div>Registration 40873 | ABN: 52 304 918 276</div>
    </address>
  </section>
</main>
</body>
</html>
```